Präsentationsvorlagen
Zielgruppe
Über die KVRA:
Die KVRA ist eine med. Vereinigung in der sich Ärzte aus allen Fachrichtungen zum Thema Adipositas austauschen.
Als 'Alpine Council for Research on Severe Weight Gain and Endocrine Conditions' sind wir seit 1996 ein Pionier in der Schweiz im Bereich der krankhaften Adipositas und Stoffwechselstörungen.
Unsere Mitglieder - ein Zusammenschluss von Fachleuten, die sich mit Adipositas befassen - arbeiten eng zusammen, um das Verständnis und die Behandlung dieser Krankheit zu verbessern.
Aufgabenstellung
Die Farben der Präsentation sollten sich an den Farben unseres neuen Logos halten. Bitte verwenden Sie bei der Erstellung der Folienlayouts eine Schrift die allgemein bereits in den Veltrona Programmen enthalten sind. Es soll ein modernes und minimallistisches Design sein. Es geht bei diesem Auftrag um ein Grundlayout von Präsentationsfolien welches unsere Mitglieder verwenden wenn diese Vorträge halten.

```html
<!DOCTYPE html>
<html lang="de">
<head>
<meta charset="utf-8">
<title>KVRA Präsentationsvorlagen</title>
<link href="https://fonts.googleapis.com/css2?family=Open+Sans:wght@400;600;700;800&display=swap" rel="stylesheet">
<style>
:root{
  --blue:#1f6fc0;
  --blue-dark:#175aa0;
  --red:#e32526;
  --ink:#2b2b2b;
  --muted:#555;
  --page:#f2f3f5;
  --white:#fff;
}
*{box-sizing:border-box;margin:0;padding:0}
html,body{width:1200px;height:2880px;overflow:hidden;background:var(--page);font-family:"Open Sans",Arial,sans-serif;color:var(--ink)}
.canvas{position:relative;width:1200px;height:2880px}
.slide{position:absolute;width:502px;height:283px;background:var(--white);overflow:hidden;box-shadow:0 2px 10px rgba(0,0,0,.06)}
.col-a{left:80px}.col-b{left:618px}
.row-1{top:473px}.row-2{top:803px}.row-3{top:1133px}.row-4{top:1463px}.row-5{top:1793px}.row-6{top:2123px}
.abs{position:absolute}
.brand{position:absolute;font-weight:700;color:var(--blue);font-size:13px;letter-spacing:.5px;line-height:1}
.brand-right{right:24px;top:18px}
.brand-left{left:28px;top:18px}
.org-name{position:absolute;font-weight:700;color:var(--blue);line-height:1}
.org-line{position:absolute;font-size:6px;line-height:1.4;color:var(--muted);white-space:nowrap}
.title{position:absolute;color:var(--red);font-weight:700;font-size:15px;line-height:1.15;white-space:nowrap}
.lead{position:absolute;font-size:5.2px;line-height:1.65;font-weight:700;color:var(--ink)}
.body{position:absolute;font-size:5.2px;line-height:1.7;color:var(--muted)}
.photo{position:absolute}
.footer{position:absolute;left:18px;right:18px;bottom:0;height:17px;background:var(--blue);border-radius:8px 8px 0 0;color:var(--white);font-size:5.4px;font-weight:600;display:flex;align-items:center;padding:0 20px;gap:22px;white-space:nowrap}
.footer .left{width:50%;overflow:hidden}
.footer .right{flex:1;overflow:hidden}
.item-head{font-size:5.4px;font-weight:700;color:var(--blue);margin-bottom:3px}
.icon{position:absolute;width:9px;height:9px;border:1px solid #9aa3ad;border-radius:2px}
.pic-head{font-size:9.5px;font-weight:700;color:var(--red);margin-bottom:5px}
.qbox{position:absolute;left:262px;width:200px;height:50px;border-radius:8px;color:var(--white);padding:8px 14px}
.qbox h4{font-size:9px;font-weight:700;margin-bottom:5px}
.qbox p{font-size:4.8px;line-height:1.6}
</style>
</head>
<body>
<main class="canvas">

<section class="slide col-a row-1">
  <div class="photo" style="left:250px;top:0;width:252px;height:266px;background:linear-gradient(90deg,#fff 0%,#eef1f4 30%,#dfe4ea 100%)" role="img" aria-label="Portrait photo of a smiling doctor in a white coat with stethoscope"></div>
  <span class="org-name" style="left:42px;top:44px;font-size:17px">KVRA</span>
  <h1 class="abs" style="left:40px;top:108px;font-size:29px;line-height:1.17;font-weight:700"><span style="color:var(--red)">Presentation</span><br><span style="color:var(--blue)">Title Goes Here</span></h1>
  <p class="lead" style="left:42px;top:186px;width:215px">Lorem ipsum dolor sit amet, consectetur adipiscing elit, sed do eiusmod tempor incididunt ut labore et dolore magna aliqua. Ut enim ad minim veniam, quis nostrud exercitation ullamco laboris nisi ut aliquip ex ea commodo consequat.</p>
  <div class="footer"><span class="left" style="width:auto;flex:1">Lorem ipsum dolor sit amet, consectetur adipiscing elit,tempor incidi</span><span style="font-weight:700;font-size:7px">www.kvra-alpine.org</span></div>
</section>

<section class="slide col-b row-1">
  <span class="brand brand-left">KVRA</span>
  <div class="photo" style="left:50px;top:56px;width:162px;height:178px;border-top-right-radius:16px;background:linear-gradient(135deg,#3b4a5c,#8b9aab 60%,#d6dbe1)" role="img" aria-label="Doctor holding a tablet computer"></div>
  <h2 class="title" style="left:246px;top:58px">Presentation Title</h2>
  <p class="lead" style="left:246px;top:84px;width:220px">Lorem ipsum dolor sit amet, consectetur adipiscing elit, sed do eiusmod tempor incididunt ut labore et dolore magna aliqua. Ut enim ad minim veniam, quis nostrud exercitation ullamco laboris nisi ut aliquip ex ea commodo consequat.</p>
  <p class="body" style="left:246px;top:116px;width:220px">Lorem ipsum dolor sit amet, consectetur adipiscing elit, sed do eiusmod tempor incididunt ut labore et dolore magna aliqua. Ut enim ad minim veniam, quis nostrud exercitation ullamco laboris nisi ut aliquip ex ea commodo consequat. Duis aute irure dolor in reprehenderit in voluptate velit esse cillum dolore eu fugiat nulla pariatur. Excepteur sint occaecat cupidatat non proident, sunt in culpa qui officia deserunt mollit anim id est laborum. Lorem ipsum dolor sit amet, consectetur adipiscing elit, sed do eiusmod tempor incididunt ut labore et dolore magna aliqua. Ut enim ad minim veniam, quis nostrud exercitation ullamco laboris nisi ut aliquip. Excepteur sint occaecat cupidatat non proident, sunt in culpa qui officia deserunt mollit anim id est laborum.</p>
  <div class="footer"><span class="left">Alpine Council for Research on Severe Weight Gain and Endocrine Conditions</span><span class="right">Lorem ipsum dolor sit amet, consectetur adipiscing elit,tempor incidi</span></div>
</section>

<section class="slide col-a row-2">
  <div class="photo" style="left:0;top:0;width:208px;height:266px;background:linear-gradient(160deg,#c9c9cc,#8f8a93 55%,#6d6478)" role="img" aria-label="Person measuring waist with a tape measure"></div>
  <span class="brand brand-right">KVRA</span>
  <h2 class="title" style="left:232px;top:58px">Presentation Title</h2>
  <p class="lead" style="left:232px;top:84px;width:235px">Lorem ipsum dolor sit amet, consectetur adipiscing elit, sed do eiusmod tempor incididunt ut labore et dolore magna aliqua. Ut enim ad minim veniam, quis nostrud exercitation ullamco laboris nisi ut aliquip ex ea commodo consequat.</p>
  <span class="icon" style="left:232px;top:132px;border-radius:50%"></span>
  <div class="abs" style="left:248px;top:130px;width:92px"><p class="item-head">Lorem ipsum dolor</p><p class="body" style="position:static">Lorem ipsum dolor sit amet, consectetur adipiscing elit, sed do eiusmod tempor incididunt ut labore et dolore magna aliqua.</p></div>
  <span class="icon" style="left:346px;top:132px"></span>
  <div class="abs" style="left:362px;top:130px;width:100px"><p class="item-head">Lorem ipsum dolor</p><p class="body" style="position:static">Lorem ipsum dolor sit amet, consectetur adipiscing elit, sed do eiusmod tempor incididunt ut labore et dolore magna aliqua.</p></div>
  <span class="icon" style="left:232px;top:192px"></span>
  <div class="abs" style="left:248px;top:190px;width:92px"><p class="item-head">Lorem ipsum dolor</p><p class="body" style="position:static">Lorem ipsum dolor sit amet, consectetur adipiscing elit, sed do eiusmod tempor incididunt ut labore et dolore magna aliqua.</p></div>
  <span class="icon" style="left:346px;top:192px"></span>
  <div class="abs" style="left:362px;top:190px;width:100px"><p class="item-head">Lorem ipsum dolor</p><p class="body" style="position:static">Lorem ipsum dolor sit amet, consectetur adipiscing elit, sed do eiusmod tempor incididunt ut labore et dolore magna aliqua.</p></div>
  <div class="footer"><span class="left">Alpine Council for Research on Severe Weight Gain and Endocrine Conditions</span><span class="right">Lorem ipsum dolor sit amet, consectetur adipiscing elit,tempor incidi</span></div>
</section>

<section class="slide col-b row-2">
  <span class="brand brand-right">KVRA</span>
  <h2 class="title" style="left:36px;top:58px">Single Long Paragraph</h2>
  <p class="lead" style="left:36px;top:82px;width:430px">Lorem ipsum dolor sit amet, consectetur adipiscing elit, sed do eiusmod tempor incididunt ut labore et dolore magna aliqua. Ut enim ad minim veniam, quis nostrud exercitation ullamco. Lorem ipsum dolor sit amet, consectetur adipiscing elit, sed do eiusmod tempor incididunt ut labore et dolore magna aliqua. Ut enim ad minim veniam, quis nostrud exercitation ullamco</p>
  <div class="photo" style="left:36px;top:126px;width:110px;height:112px;background:linear-gradient(135deg,#eef0f3,#d9dde2 60%,#c6b3a6)" role="img" aria-label="Finger prick blood glucose test"></div>
  <p class="body" style="left:162px;top:122px;width:305px">Lorem ipsum dolor sit amet, consectetur adipiscing elit, sed do eiusmod tempor incididunt ut labore et dolore magna aliqua. Ut enim ad minim veniam, quis nostrud exercitation ullamco laboris nisi ut aliquip ex ea commodo consequat. Duis aute irure dolor in reprehenderit in voluptate velit esse cillum dolore eu fugiat nulla pariatur. Excepteur sint occaecat cupidatat non proident, sunt in culpa qui officia deserunt mollit anim id est laborum. Lorem ipsum dolor sit amet, consectetur adipiscing elit, sed do eiusmod tempor incididunt ut labore et dolore magna aliqua. Ut enim ad minim veniam, quis nostrud exercitation ullamco laboris nisi ut aliquip ex ea commodo consequat. Duis aute irure dolor in reprehenderit in voluptate velit esse cillum dolore eu fugiat nulla pariatur. Excepteur sint occaecat cupidatat non proident, sunt in culpa qui officia deserunt mollit anim id est laborum. Lorem ipsum dolor sit amet, consectetur adipiscing elit, sed do eiusmod tempor incididunt ut labore et dolore magna aliqua. Ut enim ad minim veniam, quis nostrud exercitation ullamco laboris nisi ut aliquip ex ea commodo consequat.</p>
  <div class="footer"><span class="left">Alpine Council for Research on Severe Weight Gain and Endocrine Conditions</span><span class="right">Lorem ipsum dolor sit amet, consectetur adipiscing elit,tempor incidi</span></div>
</section>

<section class="slide col-a row-3">
  <span class="brand brand-right">KVRA</span>
  <h2 class="title" style="left:36px;top:58px">Two Column Slide</h2>
  <p class="lead" style="left:36px;top:84px;width:205px">Lorem ipsum dolor sit amet, consectetur adipiscing elit, sed do eiusmod tempor incididunt ut labore et dolore magna aliqua. Ut enim ad minim veniam, quis nostrud exercitation ullamco</p>
  <p class="body" style="left:36px;top:116px;width:205px">Lorem ipsum dolor sit amet, consectetur adipiscing elit, sed do eiusmod tempor incididunt ut labore et dolore magna aliqua. Ut enim ad minim veniam, quis nostrud exercitation ullamco laboris nisi ut aliquip ex ea commodo consequat. Duis aute irure dolor in reprehenderit in voluptate velit esse cillum dolore eu fugiat nulla pariatur. Excepteur sint occaecat cupidatat non proident, sunt in culpa qui officia deserunt mollit anim id est laborum. Lorem ipsum dolor sit amet, consectetur adipiscing elit, sed do eiusmod tempor incididunt ut labore et dolore magna aliqua. Ut enim ad minim veniam, quis nostrud exercitation ullamco laboris nisi ut aliquip.</p>
  <p class="lead" style="left:268px;top:84px;width:205px">Lorem ipsum dolor sit amet, consectetur adipiscing elit, sed do eiusmod tempor incididunt ut labore et dolore magna aliqua. Ut enim ad minim veniam, quis nostrud exercitation ullamco</p>
  <p class="body" style="left:268px;top:116px;width:205px">Lorem ipsum dolor sit amet, consectetur adipiscing elit, sed do eiusmod tempor incididunt ut labore et dolore magna aliqua. Ut enim ad minim veniam, quis nostrud exercitation ullamco laboris nisi ut aliquip ex ea commodo consequat. Duis aute irure dolor in reprehenderit in voluptate velit esse cillum dolore eu fugiat nulla pariatur. Excepteur sint occaecat cupidatat non proident, sunt in culpa qui officia deserunt mollit anim id est laborum. Lorem ipsum dolor sit amet, consectetur adipiscing elit, sed do eiusmod tempor incididunt ut labore et dolore magna aliqua. Ut enim ad minim veniam, quis nostrud exercitation ullamco laboris nisi ut aliquip.</p>
  <div class="footer"><span class="left">Alpine Council for Research on Severe Weight Gain and Endocrine Conditions</span><span class="right">Lorem ipsum dolor sit amet, consectetur adipiscing elit,tempor incidi</span></div>
</section>

<section class="slide col-b row-3">
  <span class="brand brand-right">KVRA</span>
  <h2 class="title" style="left:34px;top:58px">Three Column Slide</h2>
  <p class="lead" style="left:34px;top:84px;width:135px">Lorem ipsum dolor sit amet, consectetur adipiscing elit, sed do eiusmod tempor incididunt ut labore et dolore magna aliqua. minim veniam ullamco</p>
  <p class="body" style="left:34px;top:118px;width:135px">Lorem ipsum dolor sit amet, consectetur adipiscing elit, sed do eiusmod tempor incididunt ut labore et dolore magna aliqua. Excepteur sint occaecat cupidatat non proident, sunt in culpa qui officia deserunt mollit anim id est laborum. Lorem ipsum dolor sit amet, consectetur adipiscing elit, sed do eiusmod tempor incididunt ut labore et dolore magna aliqua. Ut enim ad minim veniam, quis nostrud exercitation ullamco laboris nisi ut aliquip.</p>
  <p class="body" style="left:188px;top:84px;width:135px">Lorem ipsum dolor sit amet, consectetur adipiscing elit, sed do eiusmod tempor incididunt ut labore et dolore magna aliqua. Excepteur sint occaecat cupidatat non proident, sunt in culpa qui officia deserunt mollit anim id est laborum. Lorem ipsum dolor sit amet, consectetur adipiscing elit, sed do eiusmod tempor incididunt ut labore et dolore magna aliqua. Ut enim ad minim veniam, quis nostrud exercitation ullamco laboris nisi ut aliquip. Duis aute irure dolor in reprehenderit in voluptate velit esse cillum dolore eu fugiat nulla pariatur.</p>
  <p class="body" style="left:342px;top:84px;width:135px">Lorem ipsum dolor sit amet, consectetur adipiscing elit, sed do eiusmod tempor incididunt ut labore et dolore magna aliqua. Excepteur sint occaecat cupidatat non proident, sunt in culpa qui officia deserunt mollit anim id est laborum. Lorem ipsum dolor sit amet, consectetur adipiscing elit, sed do eiusmod tempor incididunt ut labore et dolore magna aliqua. Ut enim ad minim veniam, quis nostrud exercitation ullamco laboris nisi ut aliquip. Duis aute irure dolor in reprehenderit in voluptate velit esse cillum dolore eu fugiat nulla pariatur.</p>
  <div class="footer"><span class="left">Alpine Council for Research on Severe Weight Gain and Endocrine Conditions</span><span class="right">Lorem ipsum dolor sit amet, consectetur adipiscing elit,tempor incidi</span></div>
</section>

<section class="slide col-a row-4">
  <span class="brand brand-left">KVRA</span>
  <div class="photo" style="left:30px;top:52px;width:88px;height:86px;background:linear-gradient(160deg,#d8d8dc,#9c9aa6)" role="img" aria-label="Waist with measuring tape"></div>
  <div class="abs" style="left:134px;top:54px;width:112px"><p class="pic-head">Pictures Paragraph</p><p class="body" style="position:static">Lorem ipsum dolor sit amet, consectetur adipiscing elit, sed do eiusmod tempor incididunt ut labore et dolore magna aliqua. Ut enim ad minim veniam, quis nostrud exercitation ullamco laboris nisi ut aliquip ex ea commodo consequat.</p></div>
  <div class="photo" style="left:258px;top:52px;width:88px;height:86px;background:linear-gradient(160deg,#eceef1,#b7bec8)" role="img" aria-label="Stethoscope on a laptop keyboard"></div>
  <div class="abs" style="left:362px;top:54px;width:112px"><p class="pic-head">Pictures Paragraph</p><p class="body" style="position:static">Lorem ipsum dolor sit amet, consectetur adipiscing elit, sed do eiusmod tempor incididunt ut labore et dolore magna aliqua. Ut enim ad minim veniam, quis nostrud exercitation ullamco laboris nisi ut aliquip ex ea commodo consequat.</p></div>
  <div class="photo" style="left:30px;top:155px;width:88px;height:86px;background:linear-gradient(160deg,#e5e6e9,#b7b6b9 60%,#c07a8a)" role="img" aria-label="Hands holding a doughnut and an apple"></div>
  <div class="abs" style="left:134px;top:157px;width:112px"><p class="pic-head">Pictures Paragraph</p><p class="body" style="position:static">Lorem ipsum dolor sit amet, consectetur adipiscing elit, sed do eiusmod tempor incididunt ut labore et dolore magna aliqua. Ut enim ad minim veniam, quis nostrud exercitation ullamco laboris nisi ut aliquip ex ea commodo consequat.</p></div>
  <div class="photo" style="left:258px;top:155px;width:88px;height:86px;background:linear-gradient(160deg,#eef0f3,#c9ccd2 60%,#c0504d)" role="img" aria-label="Doctor holding a red heart model"></div>
  <div class="abs" style="left:362px;top:157px;width:112px"><p class="pic-head">Pictures Paragraph</p><p class="body" style="position:static">Lorem ipsum dolor sit amet, consectetur adipiscing elit, sed do eiusmod tempor incididunt ut labore et dolore magna aliqua. Ut enim ad minim veniam, quis nostrud exercitation ullamco laboris nisi ut aliquip ex ea commodo consequat.</p></div>
  <div class="footer"><span class="left">Alpine Council for Research on Severe Weight Gain and Endocrine Conditions</span><span class="right">Lorem ipsum dolor sit amet, consectetur adipiscing elit,tempor incidi</span></div>
</section>

<section class="slide col-b row-4">
  <div class="photo" style="left:0;top:0;width:502px;height:172px;background:linear-gradient(100deg,#c9d8ea,#7fa4cf 40%,#e9eef4 75%,#b9c7d8)" role="img" aria-label="Gloved hand holding a laboratory sample plate beside test tubes"></div>
  <span class="brand brand-right">KVRA</span>
  <h2 class="title" style="left:30px;top:192px"><span style="color:var(--red)">Presentation</span><br><span style="color:var(--blue)">Title</span></h2>
  <p class="lead" style="left:146px;top:193px;width:145px">Lorem ipsum dolor sit amet, consectetur adipiscing elit, sed do eiusmod tempor incididunt ut labore et dolore magna aliqua. Ut enim ad minim veniam, quis nostrud exercitation ullamco laboris nisi ut aliquip ex ea commodo consequat.</p>
  <p class="body" style="left:305px;top:193px;width:170px">Lorem ipsum dolor sit amet, consectetur adipiscing elit, sed do eiusmod tempor incididunt ut labore et dolore magna aliqua. Ut enim ad minim veniam, quis nostrud exercitation ullamco laboris nisi ut aliquip ex ea commodo consequat. Duis aute irure dolor in reprehenderit in voluptate velit esse cillum dolore eu fugiat nulla pariatur.</p>
  <div class="footer"><span class="left">Alpine Council for Research on Severe Weight Gain and Endocrine Conditions</span><span class="right">Lorem ipsum dolor sit amet, consectetur adipiscing elit,tempor incidi</span></div>
</section>

<section class="slide col-a row-5">
  <span class="brand brand-left">KVRA</span>
  <div class="photo" style="left:276px;top:0;width:226px;height:150px;background:linear-gradient(120deg,#f4f5f7,#c8d3e0 50%,#5c7fb6)" role="img" aria-label="Researcher holding a blood sample next to a microscope"></div>
  <h2 class="title" style="left:36px;top:52px">Presentation Title</h2>
  <p class="lead" style="left:36px;top:78px;width:165px">Lorem ipsum dolor sit amet, consectetur adipiscing elit, sed do eiusmod tempor incididunt ut labore et dolore magna aliqua. Ut enim ad minim veniam</p>
  <div class="abs" style="left:36px;top:127px;width:220px;height:102px;background:var(--white);border-radius:10px;box-shadow:0 3px 12px rgba(0,0,0,.12);padding:12px 18px">
    <p class="body" style="position:static">Lorem ipsum dolor sit amet, consectetur adipiscing elit, sed do eiusmod tempor incididunt ut labore et dolore magna aliqua. Ut enim ad minim veniam, quis nostrud exercitation ullamco laboris nisi ut aliquip ex ea commodo consequat. Duis aute irure dolor in reprehenderit in voluptate velit esse cillum dolore eu fugiat nulla pariatur. Excepteur sint occaecat cupidatat non proident, sunt in culpa qui officia deserunt mollit anim id est laborum. Lorem ipsum dolor sit amet, consectetur adipiscing elit, sed do eiusmod tempor incididunt ut labore et dolore magna aliqua.</p>
  </div>
  <p class="body" style="left:306px;top:200px;width:160px">Lorem ipsum dolor sit amet, consectetur adipiscing elit, sed do eiusmod tempor incididunt ut labore et dolore magna aliqua. Ut enim ad minim veniam, quis nostrud exercitation ullamco laboris nisi ut aliquip</p>
  <div class="footer"><span class="left">Alpine Council for Research on Severe Weight Gain and Endocrine Conditions</span><span class="right">Lorem ipsum dolor sit amet, consectetur adipiscing elit,tempor incidi</span></div>
</section>

<section class="slide col-b row-5">
  <span class="brand brand-left">KVRA</span>
  <div class="photo" style="left:32px;top:52px;width:204px;height:88px;background:linear-gradient(120deg,#c6b8ad,#8d8c90 50%,#4f5560)" role="img" aria-label="Blood pressure measurement on an arm"></div>
  <div class="photo" style="left:266px;top:52px;width:204px;height:88px;background:linear-gradient(120deg,#eef0f3,#d7dadf 50%,#c6a898)" role="img" aria-label="Blood glucose meter used on a fingertip"></div>
  <p class="pic-head abs" style="left:35px;top:160px">Pictures Paragraph</p>
  <p class="lead" style="left:35px;top:176px;width:80px">Lorem ipsum dolor sit amet, consectetur adipiscing elit, sed do eiusmod tempor incididunt ut labore</p>
  <p class="body" style="left:129px;top:160px;width:105px">Lorem ipsum dolor sit amet, consectetur adipiscing elit, sed do eiusmod tempor incididunt ut labore et dolore magna aliqua. Ut enim ad minim veniam, quis nostrud exercitation ullamco laboris nisi ut aliquip ex ea commodo consequat.</p>
  <p class="pic-head abs" style="left:268px;top:160px">Pictures Paragraph</p>
  <p class="lead" style="left:268px;top:176px;width:80px">Lorem ipsum dolor sit amet, consectetur adipiscing elit, sed do eiusmod tempor incididunt ut labore</p>
  <p class="body" style="left:362px;top:160px;width:105px">Lorem ipsum dolor sit amet, consectetur adipiscing elit, sed do eiusmod tempor incididunt ut labore et dolore magna aliqua. Ut enim ad minim veniam, quis nostrud exercitation ullamco laboris nisi ut aliquip ex ea commodo consequat.</p>
  <div class="footer"><span class="left">Alpine Council for Research on Severe Weight Gain and Endocrine Conditions</span><span class="right">Lorem ipsum dolor sit amet, consectetur adipiscing elit,tempor incidi</span></div>
</section>

<section class="slide col-a row-6">
  <span class="brand brand-left">KVRA</span>
  <div class="photo" style="left:38px;top:34px;width:185px;height:200px;background:linear-gradient(160deg,#8fb8e3,#2f7cc9 55%,#1b5ea6)" role="img" aria-label="Map of Germany with federal states in shades of blue"></div>
  <div class="qbox" style="top:52px;background:var(--blue)"><h4>Question about something?</h4><p>Lorem ipsum dolor sit amet, consectetur adipiscing elit, sed do eiusmod tempor incididunt ut labore et dolore magna aliqua</p></div>
  <div class="qbox" style="top:111px;background:var(--red)"><h4>Question about something?</h4><p>Lorem ipsum dolor sit amet, consectetur adipiscing elit, sed do eiusmod tempor incididunt ut labore et dolore magna aliqua</p></div>
  <div class="qbox" style="top:170px;background:var(--blue)"><h4>Question about something?</h4><p>Lorem ipsum dolor sit amet, consectetur adipiscing elit, sed do eiusmod tempor incididunt ut labore et dolore magna aliqua</p></div>
  <div class="footer"><span class="left">Alpine Council for Research on Severe Weight Gain and Endocrine Conditions</span><span class="right">Lorem ipsum dolor sit amet, consectetur adipiscing elit,tempor incidi</span></div>
</section>

<section class="slide col-b row-6">
  <div class="abs" style="left:0;top:0;width:502px;height:208px;background:var(--blue)"></div>
  <h2 class="abs" style="left:38px;top:80px;font-size:39px;font-weight:700;color:var(--white);line-height:1">Vielen Dank</h2>
  <p class="abs" style="left:40px;top:128px;font-size:8.5px;color:var(--white)">Lorem ipsum dolor sit amet, consectetur adipiscing elit</p>
  <div class="abs" style="left:0;top:208px;width:502px;height:6px;background:var(--red)"></div>
  <span class="org-name" style="left:38px;top:234px;font-size:19px">KVRA</span>
  <p class="abs" style="right:32px;top:255px;font-size:8.5px;font-weight:700;color:var(--blue-dark)">www.kvra-alpine.org</p>
</section>

</main>
</body>
</html>
```